Brantor Works Business Card

Modern and Professional Business Card for a Med size construction/development company.

See the samples below for the design I like … but I need ideas for incorporating the red company logo while still keeping the clean look of the card samples that are attached.

Logo and tag line on the back … info on the front.

Tagline: Quality Starts from the Ground Up

Target Market(s)

Med-Large General Contractors

Contact Information for Business Card

Brantor Works Limited
42 Fenwick Avenue
Mt. Pearl, NL
A1N 4R9

t: 709-555-0147
f: 709-555-0182
w: www.brantorworks-example.com

Font styles to use
Sans Serif

Colors
fbee3e

Requirements
Must have
• I like the black and yellow designs of the attached samples …. but I'm not sure how to incorporate the red Brantor Works logo into that design??
Nice to have
• Construction safety strips

```html
<!DOCTYPE html>
<html lang="en">
<head>
<meta charset="utf-8">
<title>Brantor Works Business Card</title>
<link href="https://fonts.googleapis.com/css2?family=Open+Sans:wght@400;600;700&display=swap" rel="stylesheet">
<style>
  :root {
    --backdrop: #9a9a9a;
    --card-dark: #2a2a2a;
    --card-light: #ffffff;
    --brand-red: #e31e24;
    --text-grey: #555555;
    --text-white: #ffffff;
  }
  * { margin: 0; padding: 0; box-sizing: border-box; }
  html, body {
    width: 1133px;
    height: 1200px;
    overflow: hidden;
    background: var(--backdrop);
    font-family: "Open Sans", Arial, sans-serif;
  }
  .canvas {
    position: relative;
    width: 1133px;
    height: 1200px;
  }
  .card {
    position: absolute;
    left: 219px;
    width: 694px;
    height: 397px;
  }
  .card--back {
    top: 153px;
    background: var(--card-dark);
  }
  .card--front {
    top: 649px;
    background: var(--card-light);
  }
  .brand {
    position: absolute;
    display: flex;
    align-items: center;
    gap: 12px;
    color: var(--brand-red);
    font-weight: 700;
    white-space: nowrap;
    line-height: 1;
  }
  .brand__mark {
    flex: none;
    background: var(--brand-red);
  }
  .card--back .brand {
    left: 50%;
    top: 200px;
    transform: translate(-50%, -50%);
    font-size: 40px;
  }
  .card--back .brand__mark { width: 30px; height: 30px; }
  .tagline {
    position: absolute;
    left: 0;
    right: 0;
    top: 339px;
    text-align: center;
    color: var(--text-white);
    font-size: 17px;
    line-height: 22px;
    font-weight: 600;
    letter-spacing: 0.3px;
  }
  .card--front .brand {
    right: 33px;
    top: 85px;
    transform: translateY(-50%);
    font-size: 30px;
  }
  .card--front .brand__mark { width: 22px; height: 22px; }
  .contact {
    position: absolute;
    left: 34px;
    top: 203px;
    color: var(--text-grey);
    font-size: 19px;
    line-height: 25px;
  }
  .contact__name {
    color: var(--brand-red);
    font-weight: 600;
  }
  .contact__list {
    list-style: none;
    margin-top: 13px;
  }
  .contact__item {
    display: flex;
    align-items: center;
    gap: 4px;
    height: 25px;
  }
  .contact__icon {
    width: 16px;
    height: 16px;
    fill: var(--brand-red);
    flex: none;
  }
</style>
</head>
<body>
<main class="canvas">
  <section class="card card--back" aria-label="Card back">
    <div class="brand"><span class="brand__mark"></span><span>Brantor Works</span></div>
    <p class="tagline">QUALITY STARTS FROM THE GROUND UP</p>
  </section>

  <section class="card card--front" aria-label="Card front">
    <div class="brand"><span class="brand__mark"></span><span>Brantor Works</span></div>
    <div class="contact">
      <p class="contact__name">Brantor Works Limited</p>
      <p class="contact__lines">42 Fenwick Avenue<br>Harrowby, NL, A0X 1Z0</p>
      <ul class="contact__list">
        <li class="contact__item">
          <svg class="contact__icon" viewBox="0 0 24 24" aria-hidden="true"><path d="M6.6 10.8a15.1 15.1 0 0 0 6.6 6.6l2.2-2.2a1 1 0 0 1 1-.25 11.4 11.4 0 0 0 3.6.57 1 1 0 0 1 1 1V20a1 1 0 0 1-1 1A17 17 0 0 1 3 4a1 1 0 0 1 1-1h3.5a1 1 0 0 1 1 1c0 1.25.2 2.45.57 3.57a1 1 0 0 1-.25 1z"/></svg>
          <span>709-555-0147</span>
        </li>
        <li class="contact__item">
          <svg class="contact__icon" viewBox="0 0 24 24" aria-hidden="true"><path d="M7 3h10v5H7z"/><path d="M3 9h18v8h-3v-3H6v3H3z"/><path d="M7 15h10v6H7z"/></svg>
          <span>709-555-0182</span>
        </li>
        <li class="contact__item">
          <svg class="contact__icon" viewBox="0 0 24 24" aria-hidden="true"><circle cx="12" cy="12" r="9"/><path d="M12 3v18M3 12h18" stroke="#fff" stroke-width="1.5" fill="none"/></svg>
          <span>www.brantorworks-example.com</span>
        </li>
      </ul>
    </div>
  </section>
</main>
</body>
</html>
```